Corwin Ashby College of Nursing website

Nursing college needs a fresh, streamlined website. Many of the items on our website are required by accreditation organizations.

```html
<!DOCTYPE html>
<html lang="en">
<head>
<meta charset="utf-8">
<title>Corwin Ashby College of Nursing</title>
<link href="https://fonts.googleapis.com/css2?family=Lora:wght@400;700&family=Roboto:wght@400;500;700&display=swap" rel="stylesheet">
<style>
:root{
  --blue:#0d4d6b;
  --green:#0e6b57;
  --dark:#231f20;
  --purple:#6a1f6e;
  --ink:#222;
  --muted:#666;
  --pale:#e9f2f8;
  --grey:#9a9a9a;
  --white:#fff;
}
*{box-sizing:border-box;margin:0;padding:0}
html,body{width:1200px;height:4184px;overflow:hidden}
body{position:relative;background:var(--white);font-family:"Roboto",Arial,sans-serif;color:var(--ink)}
.abs{position:absolute}
.heading{font-family:"Lora",Georgia,serif;font-weight:700;color:var(--dark);font-size:58px;line-height:64px}
.dots{display:flex;gap:9px}
.dots i{width:9px;height:9px;border-radius:50%;display:block}
.dots i:nth-child(1){background:var(--blue)}.dots i:nth-child(2){background:var(--green)}
.dots i:nth-child(3){background:var(--dark)}.dots i:nth-child(4){background:var(--purple)}
.btn{position:absolute;display:flex;align-items:center;justify-content:center;border-radius:26px;color:#fff;font-size:12px;font-weight:700;text-transform:uppercase}
.stripe{position:absolute;left:0;width:1200px;height:4px;display:flex}
.stripe span{flex:1}
.stripe span:nth-child(1){background:var(--blue)}.stripe span:nth-child(2){background:var(--green)}
.stripe span:nth-child(3){background:var(--dark)}.stripe span:nth-child(4){background:var(--purple)}
/* header */
.brand{left:146px;top:22px;display:flex;align-items:center;gap:10px;font-family:"Lora",serif;font-weight:400;color:var(--dark)}
.brand-mark{width:44px;height:44px;border-radius:50%;background:var(--blue)}
.brand-name{font-size:20px;line-height:22px}
.brand-name small{display:block;font-size:13px;line-height:18px}
.nav a{position:absolute;top:0;height:81px;line-height:92px;font-size:12px;font-weight:500;color:var(--dark);text-decoration:none;text-transform:uppercase}
.nav a.active{background:var(--green);color:#fff;padding:0 18px;left:349px}
.search{left:1023px;top:32px;width:31px;height:25px;background:var(--purple)}
/* hero */
.hero-title{left:0;width:1200px;top:190px;text-align:center;font-family:"Lora",serif;font-weight:700;color:#fff;font-size:68px;line-height:70px;text-shadow:0 2px 8px rgba(0,0,0,.4)}
/* tiles */
.tiles{left:139px;top:579px;width:860px;height:240px;background:#fff}
.tile{position:absolute;top:585px;width:206px;height:237px;color:#fff;text-align:center;padding-top:24px}
.tile h3{font-size:16px;font-weight:500;margin-top:14px;text-transform:uppercase}
.tile p{font-size:11px;line-height:15px;margin:10px 10px 0}
.tile .down{position:absolute;left:87px;bottom:-14px;width:32px;height:32px;border-radius:50%;background:#fff}
/* about */
.body-text{font-size:13px;line-height:30px;color:var(--muted)}
.bullets li{list-style:none;font-size:13px;line-height:30px;color:var(--dark);padding-left:25px;position:relative}
.bullets li::before{content:"";position:absolute;left:0;top:11px;width:9px;height:9px;border-radius:50%;background:var(--green)}
.seal-name{left:97px;top:1156px;width:110px;text-align:center;font-family:"Lora",serif;font-weight:700;font-size:15px;line-height:19px;color:var(--blue)}
/* news */
.card{position:absolute;background:#fff;box-shadow:0 6px 24px rgba(13,77,107,.12)}
.card h4{font-size:20px;font-weight:500;line-height:28px;color:var(--dark)}
.card p{font-size:12.5px;line-height:24px;color:var(--muted);margin-top:10px}
.arrow{position:absolute;top:1680px;width:31px;height:31px;border:2px solid var(--dark);border-radius:50%}
/* contact */
.field{position:absolute;background:#fff;font-size:14px;color:#666;padding:18px 22px}
.info-title{left:146px;top:3680px;font-size:24px;font-weight:500;color:var(--blue)}
.col{position:absolute;top:3733px;font-size:13.5px;line-height:25.7px;color:var(--dark)}
.col div{position:relative;padding-left:32px}
.col b{font-weight:700}
.col svg{position:absolute;left:0;top:7px}
.divider{position:absolute;top:3733px;width:1px;height:322px;background:#ddd}
.social{position:absolute;top:4125px;width:32px;height:32px;border-radius:50%;background:var(--grey)}
</style>
</head>
<body>

<!-- header -->
<div class="stripe" style="top:0;height:3px"><span></span><span></span><span></span><span></span></div>
<div class="abs brand"><span class="brand-mark"></span><div class="brand-name">Corwin Ashby<small>College of Nursing</small></div></div>
<nav class="nav">
  <a class="active">Home</a>
  <a style="left:435px">About</a>
  <a style="left:502px">Academics</a>
  <a style="left:599px">Policies &amp; Handbooks</a>
  <a style="left:771px">Library</a>
  <a style="left:849px">Contact Us</a>
  <a style="left:950px">Donate</a>
</nav>
<div class="abs search"><svg width="31" height="25"><circle cx="14" cy="11" r="4" fill="none" stroke="#fff" stroke-width="2"/><line x1="17" y1="14" x2="20" y2="17" stroke="#fff" stroke-width="2"/></svg></div>

<!-- hero -->
<svg class="abs" style="left:0;top:89px" width="1200" height="545" role="img" aria-label="Graduation ceremony with graduates in blue caps and gowns">
  <defs><linearGradient id="heroFill" x1="0" y1="0" x2="0" y2="1"><stop offset="0" stop-color="#6b4a3a"/><stop offset=".45" stop-color="#3c4a72"/><stop offset="1" stop-color="#1f3a78"/></linearGradient></defs>
  <path d="M6 0H1200V210Q1185 470 900 545H150V540H6Z" fill="url(#heroFill)"/>
  <circle cx="1117" cy="200" r="3" fill="#fff"/><circle cx="1117" cy="218" r="4" fill="none" stroke="#fff" stroke-width="2"/><circle cx="1117" cy="236" r="3" fill="#fff"/>
</svg>
<div class="abs hero-title">Corwin Ashby College<br>of Nursing</div>
<div class="btn" style="left:528px;top:367px;width:146px;height:52px;background:var(--purple);border:3px solid #fff">Get Started</div>

<!-- tiles -->
<div class="abs tiles"></div>
<div class="tile" style="left:145px;background:var(--blue)">
  <svg width="40" height="40"><path d="M8 32l4-11 16-16 7 7-16 16z" fill="#fff"/></svg>
  <h3>Apply Now</h3><p>Generic BS Program (No LPN/clinical background required) LPN to RN ProgramRN to BS Program Admissions Pathway</p>
  <span class="down"><svg width="32" height="32"><circle cx="16" cy="16" r="9" fill="none" stroke="#0d4d6b" stroke-width="1.5"/><path d="M16 11v10M12 17l4 4 4-4" fill="none" stroke="#0d4d6b" stroke-width="1.5"/></svg></span>
</div>
<div class="tile" style="left:359px;background:var(--green)">
  <svg width="48" height="40"><path d="M4 38V16L24 4l20 12v22H32V26H16v12z" fill="#fff"/></svg>
  <h3>Our Successes</h3><p>CACN is an independent single-purpose institution. Its mission is to provide a dynamic career-ladder approach to nursing education to improve professional practice.</p>
  <span class="down"><svg width="32" height="32"><circle cx="16" cy="16" r="9" fill="none" stroke="#0e6b57" stroke-width="1.5"/><path d="M16 11v10M12 17l4 4 4-4" fill="none" stroke="#0e6b57" stroke-width="1.5"/></svg></span>
</div>
<div class="tile" style="left:572px;background:var(--dark)">
  <svg width="50" height="40"><rect x="18" y="2" width="14" height="10" fill="#fff"/><rect x="2" y="28" width="12" height="10" fill="#fff"/><rect x="19" y="28" width="12" height="10" fill="#fff"/><rect x="36" y="28" width="12" height="10" fill="#fff"/><path d="M25 12v8M8 28v-8h34v8M25 20v8" stroke="#fff" stroke-width="3" fill="none"/></svg>
  <h3>Demographics</h3><p>Student Demographics<br>Graduating Students</p>
  <span class="down"><svg width="32" height="32"><circle cx="16" cy="16" r="9" fill="none" stroke="#231f20" stroke-width="1.5"/><path d="M16 11v10M12 17l4 4 4-4" fill="none" stroke="#231f20" stroke-width="1.5"/></svg></span>
</div>
<div class="tile" style="left:786px;background:var(--purple)">
  <svg width="20" height="40"><circle cx="10" cy="5" r="5" fill="#fff"/><rect x="5" y="14" width="10" height="26" fill="#fff"/></svg>
  <h3>Information</h3><p>Licensure Exam Pass Rate<br>Consumer Information<br>Contact Information<br>AAS Course Information<br>Fees Information</p>
  <span class="down"><svg width="32" height="32"><circle cx="16" cy="16" r="9" fill="none" stroke="#6a1f6e" stroke-width="1.5"/><path d="M16 11v10M12 17l4 4 4-4" fill="none" stroke="#6a1f6e" stroke-width="1.5"/></svg></span>
</div>

<!-- about -->
<svg class="abs" style="left:90px;top:925px" width="420" height="440">
  <path d="M70 220A176 176 0 1 1 400 190" fill="none" stroke="var(--green)" stroke-width="3"/>
  <circle cx="234" cy="180" r="160" fill="#8a6a4e" role="img" aria-label="Three smiling nursing students"/>
  <circle cx="313" cy="330" r="102" fill="#fff"/>
  <circle cx="313" cy="330" r="96" fill="#2f4f8e" role="img" aria-label="Graduates in blue gowns"/>
  <circle cx="62" cy="250" r="62" fill="#fff"/>
</svg>
<div class="abs seal-name">Corwin<br>Ashby</div>
<div class="abs heading" style="left:565px;top:925px">About<br>The College</div>
<div class="abs dots" style="left:565px;top:1063px"><i></i><i></i><i></i><i></i></div>
<p class="abs body-text" style="left:565px;top:1114px;width:510px">The Corwin Ashby College of Nursing (CACN) was founded in 1945 as a private, non-profit College, and is at the forefront of nursing education. Accredited by ANEC (for the AAS program), CNAB (for the BS programs) and Lakeside States (for the entire College), CACN provides opportunities for a professional career in nursing through three programs:</p>
<ul class="abs bullets" style="left:565px;top:1275px;width:520px">
  <li>An accelerated LPN to RN/AAS track, which can be completed in 18 months;</li>
  <li>A generic baccalaureate in nursing program for students with no prior nursing degree, and which can be completed in 28 months;</li>
  <li>A baccalaureate in nursing completion program for registered nurses.</li>
</ul>
<div class="btn" style="left:565px;top:1421px;width:141px;height:47px;background:var(--purple)">Read More</div>

<!-- news -->
<svg class="abs" style="left:0;top:1536px" width="1200" height="797"><path d="M0 240Q60 0 380 0H1200V797H0Z" fill="var(--pale)"/></svg>
<div class="abs heading" style="left:145px;top:1662px">News &amp; updates</div>
<div class="abs dots" style="left:145px;top:1742px"><i></i><i></i><i></i><i></i></div>
<div class="arrow" style="left:981px"><svg width="27" height="27"><path d="M19 13.5H8M12 9l-4.5 4.5L12 18" fill="none" stroke="#231f20" stroke-width="2"/></svg></div>
<div class="arrow" style="left:1021px"><svg width="27" height="27"><path d="M8 13.5H19M15 9l4.5 4.5L15 18" fill="none" stroke="#231f20" stroke-width="2"/></svg></div>

<div class="card" style="left:145px;top:1786px;width:470px;height:466px">
  <div style="height:216px;background:linear-gradient(135deg,#d9d6d0,#8d8378)" role="img" aria-label="Hand writing on a form with a pen"></div>
  <div style="padding:18px 26px 0">
    <h4>NNL CPEA Pre-accreditation Public Posting Notice</h4>
    <p>The Associate Degree in Nursing Program at Corwin Ashby College of Nursing is seeking pre-accreditation status from the National Nursing League Council for Program Education Accreditation</p>
  </div>
  <div class="btn" style="left:26px;top:394px;width:142px;height:47px;background:var(--green)">Read More</div>
  <div class="abs" style="left:37px;top:463px;width:396px;height:3px;background:var(--green)"></div>
</div>
<div class="card" style="left:628px;top:1786px;width:424px;height:224px;border-left:4px solid var(--blue);padding:26px 30px 0 30px">
  <h4 style="font-size:17px;line-height:24px">Public Notice of Upcoming Accreditation Review Visit by the ANEC</h4>
  <p>Corwin Ashby College of Nursing wishes to announce that it will host a site visit for continuing accreditation</p>
  <div class="btn" style="left:30px;top:145px;width:142px;height:47px;background:var(--blue)">Read More</div>
</div>
<div class="card" style="left:628px;top:2025px;width:424px;height:227px;border-left:4px solid var(--purple);padding:34px 30px 0 30px">
  <h4 style="font-size:17px;line-height:24px">Upcoming NEST Testing</h4>
  <p style="text-align:justify">WHO WISH TO PREPARE FOR PRE-ADMISSION TESTING Corwin Ashby College of Nursing currently uses AMT's NEST (Nursing Entry Skills Test) Test.</p>
  <div class="btn" style="left:30px;top:155px;width:142px;height:47px;background:var(--purple)">Read More</div>
</div>

<!-- donation -->
<div class="abs heading" style="left:145px;top:2432px">Corwin Ashby<br>College of Nursing<br>Donation</div>
<div class="abs dots" style="left:145px;top:2642px"><i></i><i></i><i></i><i></i></div>
<p class="abs body-text" style="left:149px;top:2676px;width:473px;text-align:justify">Our College greatly appreciates your financial support. Some generous folks have given in honor of their mother who was a nurse. Others give to help support our students, many of whom work full time while caring for their families and attending school. Financial obstacles often interfere, so scholarships are invaluable. We are happy to name a scholarship for a person you would like to honor.</p>
<div class="btn" style="left:149px;top:2879px;width:142px;height:49px;background:var(--purple)">Donate Now</div>
<div class="abs" style="left:953px;top:2444px;width:197px;height:353px;border:5px solid var(--green)"></div>
<div class="abs" style="left:981px;top:2493px;width:141px;height:255px;border:5px solid var(--purple)"></div>
<div class="abs" style="left:693px;top:2553px;width:358px;height:367px;background:linear-gradient(160deg,#9cc3dc,#5f6d78)" role="img" aria-label="Laptop showing a donation page"></div>

<!-- contact -->
<svg class="abs" style="left:0;top:3021px" width="1200" height="596" role="img" aria-label="Dark blue tinted photo of nursing graduates">
  <path d="M0 0H780Q1150 60 1200 420V596H0Z" fill="#123f6a"/>
</svg>
<div class="abs" style="left:0;top:3100px;width:1200px;text-align:center;font-family:Lora,serif;font-weight:700;font-size:58px;color:#fff">Contact Us</div>
<div class="abs dots" style="left:567px;top:3177px"><i style="background:#fff"></i><i style="background:#fff"></i><i style="background:#fff"></i><i style="background:#fff"></i></div>
<div class="field" style="left:234px;top:3228px;width:359px;height:53px">First Name</div>
<div class="field" style="left:606px;top:3228px;width:359px;height:53px">Last Name</div>
<div class="field" style="left:234px;top:3293px;width:359px;height:53px">Email address</div>
<div class="field" style="left:606px;top:3293px;width:359px;height:53px">Phone Number</div>
<div class="field" style="left:234px;top:3360px;width:731px;height:112px">Message</div>
<div class="btn" style="left:528px;top:3503px;width:144px;height:50px;background:var(--green);border:3px solid #fff">Submit</div>

<!-- contact info -->
<div class="abs info-title">CONTACT INFO</div>
<div class="divider" style="left:463px"></div>
<div class="divider" style="left:783px"></div>
<div class="col" style="left:146px">
  <div><svg width="16" height="12"><path d="M0 2h6v10H0zM10 2h6v10h-6zM7 0h2v12H7z" fill="#6a1f6e"/></svg><b>Corwin Ashby College of Nursing</b></div>
  <div>310 Linden Avenue</div>
  <div>Springfield, NY 10099</div>
  <div><b>Registrar</b></div>
  <div><svg width="14" height="12"><path d="M2 0l3 3-2 2q2 4 5 5l2-2 3 3-3 2Q2 12 0 2z" fill="#6a1f6e"/></svg>(555) 014-7214/7218</div>
  <div><svg width="14" height="10"><rect width="14" height="10" fill="#6a1f6e"/><path d="M0 0l7 5 7-5" fill="none" stroke="#fff"/></svg>Registrar@corwinashby.edu</div>
  <div><b>Assistant VP of Student Support</b></div>
  <div><svg width="14" height="12"><path d="M2 0l3 3-2 2q2 4 5 5l2-2 3 3-3 2Q2 12 0 2z" fill="#6a1f6e"/></svg>(555) 014-7273</div>
  <div><svg width="14" height="10"><rect width="14" height="10" fill="#6a1f6e"/><path d="M0 0l7 5 7-5" fill="none" stroke="#fff"/></svg>Dana.Pryor@corwinashby.edu</div>
  <div><b>Financial Aid</b></div>
  <div><svg width="14" height="12"><path d="M2 0l3 3-2 2q2 4 5 5l2-2 3 3-3 2Q2 12 0 2z" fill="#6a1f6e"/></svg>(555) 014-7280</div>
  <div><svg width="14" height="10"><rect width="14" height="10" fill="#6a1f6e"/><path d="M0 0l7 5 7-5" fill="none" stroke="#fff"/></svg>Financial.Aid@corwinashby.edu</div>
</div>
<div class="col" style="left:508px">
  <div><b>Admissions</b></div>
  <div>(555) 014-7280</div>
  <div>Admission@corwinashby.edu</div>
  <div><b>Bursar</b></div>
  <div><svg width="14" height="12"><path d="M2 0l3 3-2 2q2 4 5 5l2-2 3 3-3 2Q2 12 0 2z" fill="#6a1f6e"/></svg>(555) 014-7289/7282</div>
  <div><svg width="14" height="10"><rect width="14" height="10" fill="#6a1f6e"/><path d="M0 0l7 5 7-5" fill="none" stroke="#fff"/></svg>Bursar@corwinashby.edu</div>
  <div><b>Library</b></div>
  <div><svg width="14" height="12"><path d="M2 0l3 3-2 2q2 4 5 5l2-2 3 3-3 2Q2 12 0 2z" fill="#6a1f6e"/></svg>(555) 014-7269</div>
  <div><svg width="14" height="10"><rect width="14" height="10" fill="#6a1f6e"/><path d="M0 0l7 5 7-5" fill="none" stroke="#fff"/></svg>Library@corwinashby.edu</div>
  <div><b>Information Technology</b></div>
  <div><svg width="14" height="12"><path d="M2 0l3 3-2 2q2 4 5 5l2-2 3 3-3 2Q2 12 0 2z" fill="#6a1f6e"/></svg>(555) 014-7245</div>
  <div><svg width="14" height="10"><rect width="14" height="10" fill="#6a1f6e"/><path d="M0 0l7 5 7-5" fill="none" stroke="#fff"/></svg>Support@corwinashby.edu</div>
</div>
<div class="col" style="left:820px">
  <div><b>ClearTrack</b></div>
  <div><svg width="14" height="12"><path d="M2 0l3 3-2 2q2 4 5 5l2-2 3 3-3 2Q2 12 0 2z" fill="#6a1f6e"/></svg>(555) 014-7215</div>
  <div><svg width="14" height="10"><rect width="14" height="10" fill="#6a1f6e"/><path d="M0 0l7 5 7-5" fill="none" stroke="#fff"/></svg>Rosa.Lindqvist@corwinashby.edu</div>
  <div><b>Title IX – Director of Human</b></div>
  <div><b>Resources</b></div>
  <div><svg width="14" height="12"><path d="M2 0l3 3-2 2q2 4 5 5l2-2 3 3-3 2Q2 12 0 2z" fill="#6a1f6e"/></svg>(555) 014-7278</div>
  <div><svg width="14" height="10"><rect width="14" height="10" fill="#6a1f6e"/><path d="M0 0l7 5 7-5" fill="none" stroke="#fff"/></svg>Title.IX@corwinashby.edu</div>
</div>

<!-- footer -->
<div class="stripe" style="top:4100px"><span></span><span></span><span></span><span></span></div>
<div class="abs" style="left:146px;top:4133px;font-size:13.5px;color:var(--dark)">© 2024 Corwin Ashby College of Nursing . All rights reserved.Privacy &nbsp;|&nbsp; Terms of Use</div>
<span class="social" style="left:897px" role="img" aria-label="Social profile link"></span>
<span class="social" style="left:937px" role="img" aria-label="Social profile link"></span>
<span class="social" style="left:979px;background:var(--blue)" role="img" aria-label="Social profile link"></span>
<span class="social" style="left:1020px" role="img" aria-label="Social profile link"></span>

</body>
</html>
```